Business Card for a Dental Office

The design should communicate integrity, quality and reliability. We also want the card look elegant, simple, but still stand out, different from the traditional-dental-office business card.

Industry/Entity Type

Business

```html
<!DOCTYPE html>
<html lang="en">
<head>
<meta charset="utf-8">
<title>Harbor Dental Studio – Business Card</title>
<link rel="stylesheet" href="https://fonts.googleapis.com/css2?family=Open+Sans:wght@400;600&display=swap">
<style>
  :root {
    --backdrop: #4c4c4c;
    --card-white: #ffffff;
    --card-black: #000000;
    --gold: #d4c21a;
    --gold-light: #f3ea3a;
    --gold-text: #a8901c;
    --ink: #111111;
    --body-text: #555555;
    --divider: #d6d6d6;
  }
  * { box-sizing: border-box; margin: 0; padding: 0; }
  html, body { width: 1105px; height: 1200px; overflow: hidden; }
  body {
    background: var(--backdrop);
    position: relative;
    font-family: "Open Sans", Arial, sans-serif;
  }
  .card {
    position: absolute;
    left: 196px;
    width: 720px;
    height: 410px;
    overflow: hidden;
  }
  .card--front { top: 146px; background: var(--card-white); }
  .card--back { top: 603px; background: var(--card-black); }

  /* front */
  .front-wave { position: absolute; left: 0; bottom: 0; width: 720px; height: 90px; }
  .brand-lockup {
    position: absolute; left: 42px; top: 176px;
    display: flex; align-items: center; gap: 12px;
  }
  .brand-mark { width: 38px; height: 38px; background: var(--ink); flex: none; }
  .brand-name {
    font-family: "Open Sans", Arial, sans-serif;
    font-weight: 600; font-size: 19px; color: var(--ink);
    line-height: 1.1; white-space: nowrap;
  }
  .brand-tagline {
    font-family: "Open Sans", Arial, sans-serif;
    font-weight: 400; font-size: 11px; color: var(--gold-text);
    margin-top: 3px; white-space: nowrap;
  }
  .front-divider {
    position: absolute; left: 363px; top: 52px;
    width: 1px; height: 280px; background: var(--divider);
  }
  .contact { position: absolute; left: 394px; top: 64px; }
  .contact-name { font-size: 25px; font-weight: 600; color: var(--ink); line-height: 1.2; }
  .contact-role { font-size: 18px; color: var(--gold-text); margin-top: 2px; }
  .contact-address { font-size: 18px; color: var(--body-text); line-height: 26px; margin-top: 20px; }
  .contact-list { list-style: none; margin-top: 6px; }
  .contact-list li {
    display: flex; align-items: center; gap: 12px;
    font-size: 18px; color: var(--body-text); line-height: 27.6px;
  }
  .contact-list svg { width: 16px; height: 16px; fill: var(--ink); flex: none; }

  /* back */
  .back-mark {
    position: absolute; left: 80px; top: 60px;
    width: 290px; height: 290px;
    background: var(--gold);
  }
  .back-brand { position: absolute; left: 407px; top: 300px; }
  .back-brand .brand-name { font-size: 25px; color: var(--gold-light); }
  .back-brand .brand-tagline { font-size: 13px; color: var(--gold); margin-top: 4px; }
  .back-web {
    font-size: 16px; letter-spacing: 3px; color: var(--gold); margin-top: 8px;
    white-space: nowrap;
  }
</style>
</head>
<body>

<section class="card card--front">
  <div class="brand-lockup">
    <div class="brand-mark"></div>
    <div>
      <div class="brand-name">Harbor Dental Studio</div>
      <div class="brand-tagline">Gentle care for every family</div>
    </div>
  </div>

  <div class="front-divider"></div>

  <div class="contact">
    <h1 class="contact-name">Daniel Reyes</h1>
    <p class="contact-role">CEO/Founder</p>
    <p class="contact-address">2140 Maple Ridge Road<br>Fairview, Oregon 97024</p>
    <ul class="contact-list">
      <li><svg viewBox="0 0 16 16"><path d="M3 1l3 3-1.5 2a9 9 0 0 0 5.5 5.5L12 10l3 3-2 2C7 15 1 9 1 3z"/></svg>503 218 4406</li>
      <li><svg viewBox="0 0 16 16"><path d="M4 0h8v16H4zM5.5 2v10h5V2zM7 13.5h2v1H7z" fill-rule="evenodd"/></svg>503 771 2903</li>
      <li><svg viewBox="0 0 16 16"><path d="M4 1h8v4H4zM1 6h14v7h-3v2H4v-2H1zM5 11v3h6v-3z" fill-rule="evenodd"/></svg>503 218 4410</li>
      <li><svg viewBox="0 0 16 16"><path d="M1 3h14v10H1zM2 4.5v.5l6 4 6-4v-.5z" fill-rule="evenodd"/></svg>hello@harbordental.com</li>
      <li><svg viewBox="0 0 16 16"><path d="M8 1a7 7 0 1 0 0 14A7 7 0 0 0 8 1zm-1 2c-1 1-2 2-1 3s2 0 2 2-2 1-2 3v2a5 5 0 0 1 1-10zm3 1a5 5 0 0 1 2 7c-1-1-2-1-2-3 0-1 1-1 1-2s-1-1-1-2z"/></svg>www.harbordental.com</li>
    </ul>
  </div>

  <svg class="front-wave" viewBox="0 0 720 90" preserveAspectRatio="none" aria-hidden="true">
    <path d="M0 14 Q360 104 720 14 V90 H0 Z" fill="var(--card-black)"/>
    <path d="M30 26 Q360 96 690 26 Q360 86 30 26 Z" fill="var(--gold-light)"/>
  </svg>
</section>

<section class="card card--back">
  <div class="back-mark"></div>
  <div class="back-brand">
    <div class="brand-name">Harbor Dental Studio</div>
    <div class="brand-tagline">Gentle care for every family</div>
    <div class="back-web">www.harbordental.com</div>
  </div>
</section>

</body>
</html>
```